New Business Card Design Project LORVANTI-Italy

we are LORVANTI-Italy
our company in the market for 3 years we are luxury cosmetic company and its about time for a facelift :)
i will like to have elegant luxurious and unique business card
that will give the person that get it a unique, luxurious and elegant impression
I'm VERY OPEN FOR NEW IDEAS , even duo i add a few files of things that i see on line and i like them

i add my logo as well
my website is LORVANTI.COM
(if you would like to see the main style that we have)

Target Market(s)

adult that have money :)

Industry/Entity Type

Business

Contact Information for Business Card

Name - Dario Lorvanti
Position - CEO and CO Founder
address - 4817 E Halvern
telephone - 555-384-1926
email - dario@lorvanti.com
fax - 555-384-1926
website - LORVANTI.COM

Colors
000000
959595
fbee3e
ffffff

Requirements
Must have
• big logo in GOLD color
• elegant look
• impressive
Nice to have
• not must but maybe classy pattern background
• not must but maybe emblem
• maybe clear plastic business card
Should not have
• colors
• images

```html
<!DOCTYPE html>
<html lang="en">
<head>
<meta charset="utf-8">
<title>LORVANTI Italy – Business Card</title>
<link href="https://fonts.googleapis.com/css2?family=Cormorant+Garamond:wght@600&family=Montserrat:wght@400;600&display=swap" rel="stylesheet">
<style>
  :root {
    --stage: #1b1b1b;
    --card-black: #1e1e1e;
    --card-white: #ffffff;
    --gold: #c9a23a;
    --gold-deep: #b38b26;
    --grey: #7a7a7a;
    --grey-light: #959595;
  }
  * { box-sizing: border-box; margin: 0; padding: 0; }
  html, body {
    width: 1200px; height: 833px; overflow: hidden;
    background: var(--stage);
  }
  .stage {
    width: 1200px; height: 833px;
    display: flex; align-items: center; justify-content: center; gap: 40px;
  }
  .card {
    width: 520px; height: 297px;
    position: relative;
    box-shadow: 0 18px 40px rgba(0,0,0,.55);
  }
  .card--front {
    background: var(--card-black);
    display: flex; flex-direction: column; align-items: center; justify-content: center;
    border-bottom: 4px solid var(--gold-deep);
  }
  .card--back {
    background: var(--card-white);
    display: flex; align-items: center;
    border-bottom: 4px solid var(--gold-deep);
  }
  .brand {
    display: flex; flex-direction: column; align-items: center;
  }
  .brand__mark {
    border: 3px solid var(--gold);
    border-radius: 50%;
  }
  .brand__name {
    font-family: "Cormorant Garamond", Georgia, serif;
    font-weight: 600;
    color: var(--gold);
    letter-spacing: 1px;
    line-height: 1;
  }
  .card--front .brand__mark { width: 92px; height: 92px; margin-bottom: 22px; }
  .card--front .brand__name { font-size: 50px; }

  .card--back .brand {
    width: 270px;
  }
  .card--back .brand__mark { width: 76px; height: 76px; margin-bottom: 16px; }
  .card--back .brand__name { font-size: 40px; }

  .divider {
    width: 2px; height: 170px; background: var(--gold);
  }
  .contact {
    padding-left: 22px;
    font-family: "Montserrat", Arial, sans-serif;
    color: var(--grey);
  }
  .contact__name {
    font-weight: 600; font-size: 20px; color: var(--gold); line-height: 1.1;
  }
  .contact__title { font-size: 13px; color: var(--grey-light); margin-bottom: 14px; }
  .contact__address { font-size: 13px; line-height: 1.35; margin-bottom: 12px; }
  .contact__list { list-style: none; font-size: 13px; line-height: 1.45; }
  .contact__list li { display: flex; align-items: center; gap: 7px; }
  .contact__list svg { width: 11px; height: 11px; fill: none; stroke: var(--gold); stroke-width: 2; flex: none; }
</style>
</head>
<body>
<main class="stage">
  <section class="card card--front">
    <div class="brand">
      <div class="brand__mark"></div>
      <span class="brand__name">LORVANTI</span>
    </div>
  </section>

  <section class="card card--back">
    <div class="brand">
      <div class="brand__mark"></div>
      <span class="brand__name">LORVANTI</span>
    </div>
    <div class="divider"></div>
    <div class="contact">
      <p class="contact__name">Elena Varesi</p>
      <p class="contact__title">Managing Partner</p>
      <p class="contact__address">Street Name Ave, Suite 100<br>State, Zip Code, Country</p>
      <ul class="contact__list">
        <li><svg viewBox="0 0 12 12"><path d="M3 1 L5 4 L4 5 Q5 7 7 8 L8 7 L11 9 L10 11 Q4 11 1 2 Z"/></svg>012-345-6789</li>
        <li><svg viewBox="0 0 12 12"><rect x="3" y="1" width="6" height="10" rx="1"/></svg>012-345-6780</li>
        <li><svg viewBox="0 0 12 12"><rect x="1" y="3" width="10" height="7"/><path d="M1 3 L6 7 L11 3"/></svg>info@yourwebsite.com</li>
        <li><svg viewBox="0 0 12 12"><circle cx="6" cy="6" r="5"/><path d="M1 6 H11 M6 1 Q3 6 6 11 M6 1 Q9 6 6 11"/></svg>yourwebsite.com</li>
      </ul>
    </div>
  </section>
</main>
</body>
</html>
```